Brackwell Yard Services Flyer Design

I need a new flyer design for my business, Brackwell Yard Services. I’ll be providing my old flyer and logo as references. The new flyer should feature updated wording, contact information, logos, and photos, but still keep the original “What We Do” section and include the phrase “Don’t See? Just Ask!” somewhere near the services. The flyer needs to look great in black and white for door-to-door handouts but also be eye-catching and professional enough for social media use.

The updated content should include the headline “Transforming Outdoor Spaces with Hard Work & Precision” and highlight three main service areas: Landscaping Services (project-based landscaping to clean, prepare, and transform outdoor spaces with precision), Property Cleanup (quick hauls, debris removal, or full cleanouts—no job too big or small), and Ground Preparation (pad preparation, brush removal, and fire lines—making properties safe, functional, and project-ready).

Please also include a “Why Choose Us?” section that lists: Locally owned since 2022, Reliable & affordable – no corners cut, Professional results you can trust, LICENSED AND Insured, and Quality work / on time / references / flexible / follow-up.

At the bottom, include the contact details: Call or Text Today!
www.brackwellyard.example
| sales@brackwellyard.example
| (555) 014-7293

The overall design should be clean, professional, and easy to read with a layout that clearly shows what we offer. Use visuals that represent outdoor services, landscaping, and property cleanup/prep work. I want something that feels trustworthy, family-friendly, and modern.
Use the same photo of leaf clean up from the original flyer if possible.
Our company colors are also black and white. For the most part.

```html
<!DOCTYPE html>
<html lang="en">
<head>
<meta charset="utf-8">
<title>Brackwell Yard Services Flyer</title>
<link href="https://fonts.googleapis.com/css2?family=Archivo:wdth,wght@125,700;125,800;125,900&family=Poppins:ital,wght@0,500;0,600;1,400&display=swap" rel="stylesheet">
<style>
  :root{
    --ink:#0e0e0e;
    --ink-soft:#1b1b1b;
    --paper:#ececec;
    --paper-shade:#d6d6d6;
    --white:#ffffff;
    --backdrop:#8a8a8a;
    --display:"Archivo", "Arial Black", sans-serif;
    --body:"Poppins", Arial, sans-serif;
  }
  html,body{margin:0;padding:0;}
  body{
    width:957px;height:1200px;overflow:hidden;
    background:var(--backdrop);position:relative;
  }
  .flyer{
    position:absolute;left:166px;top:151px;
    width:1121px;height:1611px;
    transform:scale(0.5567);transform-origin:0 0;
    overflow:hidden;background:var(--ink);
    font-family:var(--body);color:var(--white);
  }
  .flyer-shapes{position:absolute;inset:0;}
  .brand{
    position:absolute;left:30px;top:138px;
    font-family:var(--display);font-weight:900;font-stretch:125%;
    color:var(--white);line-height:1;
  }
  .brand-name{font-size:44px;letter-spacing:1px;}
  .brand-sub{font-size:27px;letter-spacing:3px;margin-top:8px;}
  .headline{
    position:absolute;left:31px;top:335px;margin:0;
    font-family:var(--display);font-weight:900;font-stretch:125%;
    font-size:41px;line-height:54.5px;color:var(--ink);letter-spacing:.5px;
    text-transform:uppercase;
  }
  .section-title{
    position:absolute;margin:0;width:560px;text-align:center;
    font-family:var(--display);font-weight:700;font-stretch:125%;
    font-size:36px;color:var(--white);
  }
  .divider{position:absolute;}
  .tag{
    position:absolute;height:30px;
    background:var(--white);color:var(--ink);
    clip-path:polygon(10px 0,100% 0,calc(100% - 10px) 100%,0 100%);
    font-family:var(--display);font-weight:800;font-stretch:125%;
    font-size:18px;line-height:30px;padding-left:19px;box-sizing:border-box;
    letter-spacing:.5px;
  }
  .ticks{position:absolute;margin:0;padding:0;list-style:none;}
  .ticks li{
    position:absolute;left:0;white-space:nowrap;
    font-size:16.5px;font-weight:500;line-height:24px;letter-spacing:-.2px;
    padding-left:25px;transform:translateY(-12px);
  }
  .ticks li svg{position:absolute;left:-10px;top:1px;width:22px;height:22px;}
  .ask-box{position:absolute;left:36px;top:1133px;width:512px;height:57px;}
  .ask-text{
    position:absolute;left:36px;top:1133px;width:512px;height:57px;
    text-align:center;line-height:57px;
    font-family:var(--display);font-weight:900;font-stretch:125%;
    font-size:25px;letter-spacing:2px;font-style:italic;
    color:transparent;-webkit-text-stroke:1.4px var(--white);
  }
  .service-card{
    position:absolute;left:608px;width:473px;height:234px;
    border:2.5px solid var(--white);border-radius:18px;box-sizing:border-box;
    background:var(--ink);
  }
  .service-photo{
    position:absolute;left:10px;top:12px;width:222px;height:205px;border-radius:14px;
  }
  .service-title{
    position:absolute;left:255px;top:22px;margin:0;
    font-family:var(--display);font-weight:800;font-stretch:125%;
    font-size:22px;line-height:27px;text-transform:uppercase;
  }
  .service-text{
    position:absolute;left:255px;top:85px;width:205px;margin:0;
    font-style:italic;font-weight:400;font-size:15.5px;line-height:23.5px;
  }
  .phone{
    position:absolute;left:0;width:1121px;top:1478px;text-align:center;
    font-family:var(--display);font-weight:900;font-stretch:125%;
    font-size:66px;line-height:90px;color:var(--ink);letter-spacing:1px;
  }
  .contact-row{
    position:absolute;left:0;width:1121px;top:1568px;height:36px;
    display:flex;justify-content:center;gap:48px;
  }
  .contact{
    position:relative;height:36px;line-height:36px;white-space:nowrap;
    font-size:20px;font-weight:600;color:var(--ink);padding-left:46px;
  }
  .contact svg{position:absolute;left:0;top:0;width:36px;height:36px;}
</style>
</head>
<body>
<svg width="0" height="0" style="position:absolute">
  <defs>
    <symbol id="tick" viewBox="0 0 22 22">
      <circle cx="10" cy="12" r="8" fill="none" stroke="#fff" stroke-width="2.4"/>
      <path d="M5.5 11.5l4 4L20 3" fill="none" stroke="#fff" stroke-width="3" stroke-linecap="round" stroke-linejoin="round"/>
    </symbol>
  </defs>
</svg>

<main class="flyer">
  <svg class="flyer-shapes" viewBox="0 0 1121 1611" width="1121" height="1611">
    <defs>
      <linearGradient id="paper" x1="0" y1="0" x2="1" y2="1">
        <stop offset="0" stop-color="#f1f1f1"/>
        <stop offset=".5" stop-color="#e2e2e2"/>
        <stop offset="1" stop-color="#f0f0f0"/>
      </linearGradient>
      <linearGradient id="heroPhoto" x1="0" y1="0" x2="0" y2="1">
        <stop offset="0" stop-color="#c9d6e4"/>
        <stop offset=".45" stop-color="#6f7d62"/>
        <stop offset=".7" stop-color="#8d8b86"/>
        <stop offset="1" stop-color="#a59c90"/>
      </linearGradient>
    </defs>
    <rect width="1121" height="1611" fill="var(--ink)"/>
    <polygon points="0,0 446,0 393,92 0,92" fill="url(#paper)"/>
    <polygon points="0,276 471,276 484,328 596,605 0,605" fill="url(#paper)"/>
    <polygon points="592,600 618,672 698,700 660,672" fill="url(#paper)"/>
    <polygon points="598,0 673,0 570,220 548,220" fill="url(#paper)"/>
    <line x1="596" y1="0" x2="530" y2="110" stroke="#fff" stroke-width="3"/>
    <polygon role="img" aria-label="Photo of a finished backyard with a stone retaining wall, gravel bed, paver patio and wooden fence" points="673,0 1121,0 1121,672 616,672 523,328" fill="url(#heroPhoto)"/>
    <polygon points="786,938 818,938 851,963 819,963" fill="#e6e6e6"/>
    <polygon points="936,1200 968,1200 996,1218 964,1218" fill="#e6e6e6"/>
    <polygon points="1121,1360 1121,1477 1090,1477" fill="url(#paper)"/>
    <rect x="0" y="1477" width="1121" height="134" fill="url(#paper)"/>
    <polygon points="0,1561 0,1611 61,1611" fill="var(--ink)"/>
    <polygon points="1121,1558 1121,1611 1056,1611" fill="var(--ink)"/>
  </svg>

  <div class="brand">
    <div class="brand-name">BRACKWELL</div>
    <div class="brand-sub">YARD SERVICES</div>
  </div>

  <h1 class="headline">Transforming<br>Outdoor Spaces<br>With Hard Work<br>&amp; Precision</h1>

  <h2 class="section-title" style="left:0;top:632px;">What We Do</h2>
  <svg class="divider" style="left:237px;top:687px" width="82" height="12" viewBox="0 0 82 12">
    <line x1="5" y1="6" x2="77" y2="6" stroke="#fff" stroke-width="1.5"/>
    <circle cx="4" cy="6" r="3" fill="var(--ink)" stroke="#fff" stroke-width="1.3"/>
    <circle cx="78" cy="6" r="3" fill="var(--ink)" stroke="#fff" stroke-width="1.3"/>
  </svg>

  <div class="tag" style="left:30px;top:723px;width:157px;">REMOVE</div>
  <div class="tag" style="left:364px;top:723px;width:157px;">INSTALL</div>

  <ul class="ticks" style="left:39px;top:0;">
    <li style="top:789px"><svg><use href="#tick"/></svg>Junk removal</li>
    <li style="top:823px"><svg><use href="#tick"/></svg>Trash &amp; waste hauling</li>
    <li style="top:859px"><svg><use href="#tick"/></svg>Yard and garden cleanup</li>
    <li style="top:894px"><svg><use href="#tick"/></svg>Appliance removal</li>
  </ul>
  <ul class="ticks" style="left:374px;top:0;">
    <li style="top:789px"><svg><use href="#tick"/></svg>Mulch</li>
    <li style="top:823px"><svg><use href="#tick"/></svg>D.G.</li>
    <li style="top:859px"><svg><use href="#tick"/></svg>Plants</li>
    <li style="top:894px"><svg><use href="#tick"/></svg>Rock</li>
  </ul>

  <div class="tag" style="left:30px;top:931px;width:345px;">MAINTENANCE &amp; OTHER</div>
  <ul class="ticks" style="left:39px;top:0;">
    <li style="top:996px"><svg><use href="#tick"/></svg>Yard clean up</li>
    <li style="top:1030px"><svg><use href="#tick"/></svg>Weed prevention (pre-emergent)</li>
    <li style="top:1066px"><svg><use href="#tick"/></svg>Roof &amp; gutter cleaning</li>
    <li style="top:1102px"><svg><use href="#tick"/></svg>5 Fence &amp; deck staining</li>
  </ul>

  <svg class="ask-box" viewBox="0 0 512 57">
    <polygon points="12,1.5 510,1.5 500,55.5 1.5,55.5" fill="none" stroke="#fff" stroke-width="2"/>
  </svg>
  <div class="ask-text">DON'T SEE IT, JUST ASK</div>

  <h2 class="section-title" style="left:1px;top:1202px;">Why Choose Us?</h2>
  <svg class="divider" style="left:241px;top:1257px" width="82" height="12" viewBox="0 0 82 12">
    <line x1="5" y1="6" x2="77" y2="6" stroke="#fff" stroke-width="1.5"/>
    <circle cx="4" cy="6" r="3" fill="var(--ink)" stroke="#fff" stroke-width="1.3"/>
    <circle cx="78" cy="6" r="3" fill="var(--ink)" stroke="#fff" stroke-width="1.3"/>
  </svg>

  <ul class="ticks" style="left:39px;top:0;">
    <li style="top:1301px"><svg><use href="#tick"/></svg>Locally owned since 2022</li>
    <li style="top:1337px"><svg><use href="#tick"/></svg>Reliable &amp; affordable – no corners cut</li>
    <li style="top:1378px"><svg><use href="#tick"/></svg>Professional results you can trust</li>
    <li style="top:1414px"><svg><use href="#tick"/></svg>&nbsp;Licensed And Insured</li>
    <li style="top:1454px"><svg><use href="#tick"/></svg>Quality work</li>
  </ul>
  <ul class="ticks" style="left:425px;top:0;">
    <li style="top:1301px"><svg><use href="#tick"/></svg>On time</li>
    <li style="top:1338px"><svg><use href="#tick"/></svg>References</li>
    <li style="top:1377px"><svg><use href="#tick"/></svg>Flexible</li>
    <li style="top:1415px"><svg><use href="#tick"/></svg>Follow-up</li>
  </ul>

  <section class="service-card" style="top:703px;">
    <div class="service-photo" role="img" aria-label="Photo of a landscaped backyard with gravel bed and block retaining wall" style="background:linear-gradient(180deg,#c7d3df 0%,#6e7b5f 45%,#8e8a83 75%,#a79d8f 100%);"></div>
    <h3 class="service-title">Landscaping<br>Services</h3>
    <p class="service-text">Project-based landscaping to clean, prepare, and transform outdoor spaces with precision</p>
  </section>

  <section class="service-card" style="top:965px;">
    <div class="service-photo" role="img" aria-label="Photo of a trailer loaded with cleanup debris, old rugs and scrap wood" style="background:linear-gradient(160deg,#9aa3a8 0%,#7d6b58 40%,#8e8b7d 70%,#5d6670 100%);"></div>
    <h3 class="service-title">Property<br>Cleanup</h3>
    <p class="service-text" style="top:95px;">Quick hauls, debris removal, or full cleanouts—no job too big or small</p>
  </section>

  <section class="service-card" style="top:1218px;">
    <div class="service-photo" role="img" aria-label="Photo of a cleared and prepared ground pad beside stacked pavers and a pickup truck" style="background:linear-gradient(180deg,#b9cbe0 0%,#9ea3a5 40%,#8f8878 70%,#a89c88 100%);"></div>
    <h3 class="service-title">Ground<br>Preparation</h3>
    <p class="service-text" style="top:83px;width:210px;">Pad preparation, brush removal, and fire lines—making properties safe, functional, and project-ready</p>
  </section>

  <div class="phone">(555) 014-7293</div>

  <div class="contact-row">
    <div class="contact">
      <svg viewBox="0 0 36 36">
        <circle cx="18" cy="18" r="18" fill="var(--ink)"/>
        <g fill="none" stroke="#fff" stroke-width="1.4">
          <circle cx="18" cy="18" r="8"/>
          <ellipse cx="18" cy="18" rx="3.6" ry="8"/>
          <line x1="10" y1="18" x2="26" y2="18"/>
          <line x1="11.5" y1="13.5" x2="24.5" y2="13.5"/>
          <line x1="11.5" y1="22.5" x2="24.5" y2="22.5"/>
        </g>
      </svg>
      www.brackwellyard.example
    </div>
    <div class="contact">
      <svg viewBox="0 0 36 36">
        <circle cx="18" cy="18" r="18" fill="var(--ink)"/>
        <rect x="10.5" y="12.5" width="15" height="11" rx="1.5" fill="#fff"/>
        <path d="M10.8 13l7.2 5.6 7.2-5.6" fill="none" stroke="var(--ink)" stroke-width="1.3"/>
      </svg>
      sales@brackwellyard.example
    </div>
  </div>
</main>
</body>
</html>
```